Verdana Harvest Co - Business Card Design Project

We need business cards for our business. We grow roots and fruits in Central and South America, we import and distribute in FL, USA. We do fresh and frozen products.

Target Market(s)

Small and big supermarkets, wholesalers, traders, distributors, etc

Industry/Entity Type

Business

```html
<!DOCTYPE html>
<html lang="en">
<head>
<meta charset="utf-8">
<title>Verdana Harvest Co – Business Card</title>
<link href="https://fonts.googleapis.com/css2?family=Lato:wght@300;400;700&display=swap" rel="stylesheet">
<style>
  :root {
    --leaf-green: #5f7d34;
    --harvest-orange: #f0901e;
    --card-white: #fbfbf9;
    --backdrop: #e4e4e2;
    --rule-grey: #8a9a6a;
  }
  html, body {
    margin: 0;
    padding: 0;
    width: 1200px;
    height: 818px;
    overflow: hidden;
    background: var(--backdrop);
  }
  .canvas {
    position: relative;
    width: 1200px;
    height: 818px;
    display: flex;
    align-items: center;
    justify-content: center;
  }
  .business-card {
    position: relative;
    width: 840px;
    height: 480px;
    background: var(--card-white);
    box-shadow: 0 6px 24px rgba(0,0,0,0.15);
    font-family: "Lato", sans-serif;
    overflow: hidden;
  }
  .edge-band {
    position: absolute;
    top: 0;
    width: 26px;
    height: 100%;
    display: flex;
    flex-direction: column;
  }
  .edge-band--left { left: 0; }
  .edge-band--right { right: 0; }
  .edge-band span { display: block; }
  .band-orange { background: var(--harvest-orange); }
  .band-green { background: var(--leaf-green); }
  .edge-band--left .band-orange { height: 50%; }
  .edge-band--left .band-green { height: 50%; }
  .edge-band--right .band-green { height: 48%; }
  .edge-band--right .band-orange { height: 52%; }

  .card-content {
    position: absolute;
    left: 90px;
    right: 70px;
    top: 58px;
  }
  .brand {
    display: flex;
    align-items: center;
    gap: 16px;
    margin-left: 40px;
  }
  .brand-dot {
    width: 26px;
    height: 26px;
    border-radius: 50%;
    background: var(--leaf-green);
  }
  .brand-name {
    font-size: 52px;
    font-weight: 400;
    color: var(--leaf-green);
    letter-spacing: 1px;
    line-height: 1;
  }
  .brand-rule {
    width: 470px;
    height: 1px;
    background: var(--rule-grey);
    margin: 22px 0 0 40px;
  }
  .tagline {
    margin: 16px 0 0 20px;
    font-size: 21px;
    font-weight: 400;
    color: var(--leaf-green);
  }
  .person {
    margin: 44px 0 0 180px;
  }
  .person-name {
    font-size: 30px;
    font-weight: 400;
    color: var(--harvest-orange);
    line-height: 1.1;
  }
  .person-title {
    font-size: 16px;
    font-weight: 400;
    color: var(--leaf-green);
    margin: 2px 0 0 22px;
  }
  .person-rule {
    width: 280px;
    height: 1px;
    background: var(--rule-grey);
    margin: 14px 0 0 0;
  }
  .offer {
    margin: 30px 0 0 220px;
    font-size: 24px;
    font-weight: 400;
    color: var(--leaf-green);
    line-height: 1.3;
  }
  .offer p { margin: 0; }
</style>
</head>
<body>
<main class="canvas">
  <article class="business-card">
    <div class="edge-band edge-band--left">
      <span class="band-orange"></span>
      <span class="band-green"></span>
    </div>
    <div class="edge-band edge-band--right">
      <span class="band-green"></span>
      <span class="band-orange"></span>
    </div>

    <div class="card-content">
      <div class="brand">
        <span class="brand-dot"></span>
        <span class="brand-name">Verdana Harvest Co</span>
      </div>
      <div class="brand-rule"></div>
      <p class="tagline">We grow roots and fruits in Central and South America</p>

      <div class="person">
        <div class="person-name">Employee Name</div>
        <div class="person-title">Managing Director</div>
        <div class="person-rule"></div>
      </div>

      <div class="offer">
        <p>We do fresh and frozen products</p>
        <p>we import and distribute in FL, USA</p>
      </div>
    </div>
  </article>
</main>
</body>
</html>
```